Roofing company in Toronto, Canada needs a logo design and business card design

We need a business card and logo created for our company. Our company is "KLV Roofing" which provides roofing services for commercial and residential customers. We serve customers in the Greater Toronto Area (in Canada) thus the name KLV.

We want the logo and business card to be a modern design displaying professionalism and quality in the work. We would prefer rounded corners for the business cards but are open to other ideas. The cards should be pleasant and appealing to customers.

Target Market(s)

Commercial and Residential customers

Industry/Entity Type

Roofing

Contact Information for Business Card

Logo Text

KLV Roofing

Requirements
Nice to have
• Colours that are pleasing to the eye but at the same time should stand out from other business cards. If the design can incorporate the name of KLV Roofing and the actual concept of roofing that would be nice.
Should not have
• Do not want the business cards or logo to be childish looking. Need to look professionally designed.

```html
<!DOCTYPE html>
<html lang="en">
<head>
<meta charset="utf-8">
<title>KLV Roofing – Business Card</title>
<link rel="stylesheet" href="https://fonts.googleapis.com/css2?family=Open+Sans:wght@400;600&display=swap">
<style>
  :root {
    --page-bg: #eef0f3;
    --card-blue: #1a73c4;
    --text-white: #ffffff;
    --text-soft: #e6f0fa;
    --frame-light: #e9e4e2;
    --frame-mid: #a59c98;
    --frame-dark: #6f6763;
    --window-top: #f6f1ef;
    --window-bottom: #e7dedd;
    --brand-blue: #1a73c4;
  }
  * { margin: 0; padding: 0; box-sizing: border-box; }
  html, body {
    width: 1200px; height: 900px; overflow: hidden;
    background: var(--page-bg);
    font-family: "Open Sans", sans-serif;
  }
  .business-card {
    position: absolute; left: 78px; top: 127px;
    width: 1043px; height: 646px;
    background: var(--card-blue);
    box-shadow: 0 12px 40px rgba(20, 40, 70, 0.18);
  }
  .logo-frame {
    position: absolute; left: 51px; top: 69px;
    width: 518px; height: 524px;
    padding: 9px;
    background: linear-gradient(135deg, var(--frame-light), var(--frame-mid) 35%, var(--frame-light) 60%, var(--frame-dark));
  }
  .logo-window {
    width: 100%; height: 100%;
    background: linear-gradient(160deg, var(--window-top), var(--window-bottom));
    display: flex; align-items: center; justify-content: center;
  }
  .brand-name {
    color: var(--brand-blue);
    font-weight: 600;
    font-size: 64px;
    letter-spacing: 1px;
  }
  .contact-block {
    position: absolute; left: 618px; top: 0;
    color: var(--text-white);
  }
  .person-name {
    position: absolute; top: 108px; white-space: nowrap;
    font-size: 41px; font-weight: 600;
  }
  .person-title {
    position: absolute; top: 166px; white-space: nowrap;
    font-size: 27px; color: var(--text-soft);
  }
  .contact-list { position: absolute; top: 314px; list-style: none; }
  .contact-list li {
    display: flex; align-items: center; gap: 10px;
    height: 38px; font-size: 28px; white-space: nowrap;
  }
  .contact-list svg { width: 20px; height: 20px; fill: var(--text-white); flex: none; }
  .address {
    position: absolute; top: 458px; white-space: nowrap;
    font-size: 28px; line-height: 34px; font-style: normal;
    color: var(--text-soft);
  }
</style>
</head>
<body>
  <div class="business-card">
    <div class="logo-frame">
      <div class="logo-window" role="img" aria-label="Frosted clear window panel behind the company name">
        <span class="brand-name">KLV Roofing</span>
      </div>
    </div>

    <div class="contact-block">
      <div class="person-name">Jonathan Smith</div>
      <div class="person-title">Managing Director</div>

      <ul class="contact-list">
        <li>
          <svg viewBox="0 0 24 24" aria-hidden="true"><path d="M6.6 10.8a15.1 15.1 0 0 0 6.6 6.6l2.2-2.2a1 1 0 0 1 1-.25 11.4 11.4 0 0 0 3.6.57 1 1 0 0 1 1 1V20a1 1 0 0 1-1 1A17 17 0 0 1 3 4a1 1 0 0 1 1-1h3.5a1 1 0 0 1 1 1c0 1.25.2 2.45.57 3.6a1 1 0 0 1-.25 1z"/></svg>
          (044)123456789
        </li>
        <li>
          <svg viewBox="0 0 24 24" aria-hidden="true"><path d="M2 5h20v14H2z M4 7v.4l8 5 8-5V7l-8 5z" fill-rule="evenodd"/></svg>
          info@youremail.com
        </li>
        <li>
          <svg viewBox="0 0 24 24" aria-hidden="true"><path d="M12 2a10 10 0 1 0 0 20 10 10 0 0 0 0-20zm-1 17.9A8 8 0 0 1 4.1 10L9 15v1a2 2 0 0 0 2 2zm6.9-2.5A2 2 0 0 0 16 16h-1v-3a1 1 0 0 0-1-1H8v-2h2a1 1 0 0 0 1-1V7h2a2 2 0 0 0 2-2v-.4a8 8 0 0 1 2.9 12.8z"/></svg>
          www.websitename.com
        </li>
      </ul>

      <address class="address">
        1234, Address Goes Here<br>
        Country Name, 123456
      </address>
    </div>
  </div>
</body>
</html>
```